Mental Health care Company in Washington DC

We are a new mental health care services provider in Washington DC. Please look at these sites.
https://brightwaterfamilysupport.com
https://www.quietharborinc.com
https://willowgate-dc.org/
https://www.tidepathdc.com
https://www.thelanternofdc.com

```html
<!DOCTYPE html>
<html lang="en">
<head>
<meta charset="utf-8">
<title>Vela Care Services</title>
<link href="https://fonts.googleapis.com/css2?family=Raleway:wght@400;500;600;700&display=swap" rel="stylesheet">
<style>
:root{
  --teal:#5db9be;
  --teal-light:#a3d9dc;
  --teal-text:#4fb3b9;
  --orange:#f4a462;
  --navy:#0d1b3e;
  --ink:#111111;
  --white:#ffffff;
}
*{margin:0;padding:0;box-sizing:border-box}
html,body{width:1200px;height:2750px;overflow:hidden;background:var(--white)}
body{font-family:'Raleway',sans-serif;color:var(--ink);position:relative}

/* header */
.site-header{position:absolute;top:0;left:0;width:1200px;height:92px;background:var(--white)}
.brand{position:absolute;left:138px;top:30px;display:flex;align-items:center;gap:10px}
.brand-dot{width:12px;height:12px;border-radius:50%;background:var(--orange)}
.brand-name{font-weight:600;font-size:28px;color:var(--navy);line-height:1}
.main-nav{position:absolute;top:40px;left:372px;display:flex;gap:31px;font-size:15px;font-weight:600}
.main-nav .active{color:var(--teal-text)}
.book-btn{position:absolute;left:944px;top:31px;width:118px;height:36px;background:var(--orange);color:var(--white);
  border-radius:18px 0 18px 18px;font-size:14px;font-weight:600;display:flex;align-items:center;justify-content:center;gap:7px}
.mini-dot{width:8px;height:8px;border-radius:50%;background:currentColor}

/* hero */
.hero{position:absolute;top:92px;left:0;width:1200px;height:549px;
  background:linear-gradient(110deg,#6cc3c7 0%,#5cb6bb 55%,#52aeb4 100%)}
.hero-dots{position:absolute;left:74px;top:182px;display:flex;flex-direction:column;gap:10px}
.hero-dots span{width:10px;height:10px;border-radius:50%;background:var(--white)}
.hero-dots span.on{background:var(--navy)}
.hero-title{position:absolute;left:148px;top:160px;font-size:46px;font-weight:700;color:var(--white);white-space:nowrap}
.hero-sub{position:absolute;left:150px;top:216px;font-size:22px;font-weight:700;color:var(--white);line-height:26px;width:450px}
.hero-btn{position:absolute;left:150px;top:289px;width:281px;height:47px;background:var(--navy);color:var(--white);
  border-radius:24px 24px 0 24px;font-size:19px;font-weight:600;display:flex;align-items:center;justify-content:center;gap:12px}
.hero-photo{position:absolute;left:620px;top:92px;width:386px;height:386px;border-radius:90px;
  background:linear-gradient(160deg,#c9a68a,#7a5a45 60%,#a8c5c3)}

/* about */
.about{position:absolute;left:128px;top:590px;width:945px;height:355px;background:var(--orange);
  border-radius:180px 0 180px 180px;text-align:center}
.about-kicker{margin-top:57px;font-size:26px;font-weight:600;color:var(--navy)}
.about-title{font-size:45px;font-weight:700;color:var(--navy);margin-top:2px}
.about-text{width:830px;margin:18px auto 0;font-size:15.5px;line-height:24px;color:#1f1f1f}

/* services */
.section-title{position:absolute;width:1200px;text-align:center;font-weight:700;font-size:45px;color:var(--ink)}
.services-mark{position:absolute;left:592px;top:985px;width:16px;height:16px;border-radius:50%;background:var(--orange)}
.service-card{position:absolute;top:1098px;width:287px}
.service-img{width:287px;height:219px}
.service-name{margin-top:16px;font-size:22px;font-weight:600}
.service-text{margin-top:14px;font-size:13px;line-height:19px;color:#222;padding-left:2px}
.pill-btn{display:inline-flex;align-items:center;justify-content:center;width:98px;height:36px;border-radius:18px 0 18px 18px;
  font-size:13px;font-weight:700;color:var(--ink);margin-top:14px}
.pill-orange{background:var(--orange)}
.pill-teal{background:var(--teal-light)}
.slider-arrow{position:absolute;width:60px;height:76px;background:var(--teal-light);display:flex;align-items:center;justify-content:center}

/* news */
.news-img{position:absolute;left:0;top:1568px;width:614px;height:355px;border-radius:0 0 220px 0;
  background:linear-gradient(120deg,#b9a08e,#7c5a44 45%,#c4b7ae 75%,#8e3a3a)}
.news-title{position:absolute;left:650px;top:1578px;font-size:46px;font-weight:700}
.news-date{position:absolute;left:654px;top:1652px;font-size:15px;font-weight:700}
.news-rule{position:absolute;left:752px;top:1666px;width:269px;height:1px;background:#bcdadb}
.news-text{position:absolute;left:652px;top:1686px;width:370px;font-size:14.5px;line-height:19.5px;color:#222}
.news-btn{position:absolute;left:645px;top:1811px;margin:0}
.faint-shape{position:absolute;left:1058px;top:1592px;width:142px;height:234px;border-radius:60px 0 0 60px;background:#e6e6e6}

/* testimonials */
.t-panel{position:absolute;top:2080px;width:575px;height:345px}
.t-left{left:0;background:var(--teal-light);border-radius:0 110px 0 0}
.t-right{left:626px;width:574px;background:var(--orange);border-radius:110px 0 0 0}
.stars{position:absolute;top:95px;font-size:22px;letter-spacing:5px;color:var(--ink)}
.t-quote{position:absolute;top:127px;width:320px;font-size:16px;line-height:19.5px;color:#1f1f1f}
.t-name{position:absolute;top:259px;font-size:16px;font-weight:700}

/* footer */
.site-footer{position:absolute;top:2425px;left:0;width:1200px;height:325px;background:var(--navy);color:var(--white)}
.footer-brand{position:absolute;top:95px;width:1200px;text-align:center;font-size:50px;font-weight:600;line-height:1}
.footer-nav{position:absolute;top:173px;width:1200px;display:flex;justify-content:center;gap:31px;font-size:15px;font-weight:600}
.footer-nav .active{color:var(--teal-text)}
.socials{position:absolute;top:220px;left:504px;display:flex;gap:10px}
.socials span{width:40px;height:40px;border-radius:50%;background:var(--orange)}
.socials span.on{background:var(--teal-light)}
.copyright{position:absolute;top:289px;width:1200px;text-align:center;font-size:13px;font-weight:600}
</style>
</head>
<body>

<header class="site-header">
  <div class="brand"><span class="brand-dot"></span><span class="brand-name">Vela Care</span></div>
  <nav class="main-nav">
    <span class="active">Home</span><span>About Us</span><span>Services</span><span>News and Events</span><span>Career</span><span>Contact Us</span>
  </nav>
  <div class="book-btn"><span class="mini-dot"></span>Book Now</div>
</header>

<section class="hero" role="img" aria-label="Faded photo of a therapy session in teal tones">
  <div class="hero-dots"><span></span><span class="on"></span><span></span><span></span></div>
  <h1 class="hero-title">Vela Care Services</h1>
  <p class="hero-sub">We are a Mental Health care Company in Washington DC</p>
  <div class="hero-btn"><span class="mini-dot"></span>Make an Appointment</div>
  <div class="hero-photo" role="img" aria-label="Photo of a laughing young woman"></div>
</section>

<section class="about">
  <p class="about-kicker">About</p>
  <h2 class="about-title">Vela Care Service</h2>
  <p class="about-text">Lorem ipsum dolor sit amet, consectetur adipiscing elit, sed do eiusmod tempor incididunt ut labore et dolore magna aliqua. Quis ipsum suspendisse ultrices gravida. Risus commodo viverra maecenas accumsan lacus vel facilisis. Lorem ipsum dolor sit amet, consectetur adipiscing elit, sed do eiusmod tempor incididunt ut labore et dolore magna aliqua. Quis ipsum suspendisse ultrices gravida. Risus commodo viverra maecenas accumsan lacus vel facilisis.</p>
</section>

<div class="services-mark"></div>
<h2 class="section-title" style="top:1022px">Services</h2>

<div class="slider-arrow" style="left:0;top:1224px">
  <svg width="14" height="22" viewBox="0 0 14 22"><path d="M11 2 L3 11 L11 20" stroke="#111" stroke-width="3" fill="none"/></svg>
</div>
<div class="slider-arrow" style="left:1136px;top:1193px">
  <svg width="14" height="22" viewBox="0 0 14 22"><path d="M3 2 L11 11 L3 20" stroke="#111" stroke-width="3" fill="none"/></svg>
</div>

<article class="service-card" style="left:138px">
  <div class="service-img" role="img" aria-label="Photo of two women in a therapy conversation" style="background:linear-gradient(135deg,#4a4d50,#7d7a74 50%,#9b3a3a)"></div>
  <h3 class="service-name">Individual Therapy</h3>
  <p class="service-text">Lorem ipsum dolor sit amet, consectetur adipiscing elit, sed do eiusmod tempor incididunt ut labore et dolore magna aliqua.</p>
  <span class="pill-btn pill-teal">Learn More</span>
</article>
<article class="service-card" style="left:456px">
  <div class="service-img" role="img" aria-label="Photo of a doctor talking with an older patient" style="background:linear-gradient(135deg,#c9d3d6,#eef1f2 45%,#8a8f93)"></div>
  <h3 class="service-name">Medication Management</h3>
  <p class="service-text">Lorem ipsum dolor sit amet, consectetur adipiscing elit, sed do eiusmod tempor incididunt ut labore et dolore magna aliqua.</p>
  <span class="pill-btn pill-orange">Learn More</span>
</article>
<article class="service-card" style="left:773px">
  <div class="service-img" role="img" aria-label="Photo of a psychiatrist holding a clipboard" style="background:linear-gradient(135deg,#dfe4e6,#b8c3c6 45%,#2f5a48)"></div>
  <h3 class="service-name">Psychiatry</h3>
  <p class="service-text">Lorem ipsum dolor sit amet, consectetur adipiscing elit, sed do eiusmod tempor incididunt ut labore et dolore magna aliqua.</p>
  <span class="pill-btn pill-orange">Learn More</span>
</article>

<div class="news-img" role="img" aria-label="Photo of a cheerful support group sitting together"></div>
<h2 class="news-title">News And Events</h2>
<p class="news-date">12106-2025</p>
<div class="news-rule"></div>
<p class="news-text">Lorem ipsum dolor sit amet, consectetur adipiscing elit, sed do eiusmod tempor incididunt ut labore et dolore magna aliqua. Quis ipsum suspendisse ultrices gravida. Risus commodo viverra maecenas accumsan lacus vel facilisis.</p>
<span class="pill-btn pill-teal news-btn">Learn More</span>
<div class="faint-shape"></div>

<h2 class="section-title" style="top:1990px">Testimonials</h2>

<div class="t-panel t-left">
  <div class="stars" style="left:137px">★★★★★</div>
  <p class="t-quote" style="left:137px">“Lorem ipsum dolor sit amet, consectetur adipiscing elit, sed do eiusmod tempor incididunt ut labore et dolore magna aliqua. Quis ipsum suspendisse ultrices gravida. Risus commodo viverra maecenas accumsan lacus vel facilisis. ”</p>
  <p class="t-name" style="left:137px">Nora.K</p>
</div>
<div class="t-panel t-right">
  <div class="stars" style="left:115px">★★★★★</div>
  <p class="t-quote" style="left:115px">“Lorem ipsum dolor sit amet, consectetur adipiscing elit, sed do eiusmod tempor incididunt ut labore et dolore magna aliqua. Quis ipsum suspendisse ultrices gravida. Risus commodo viverra maecenas accumsan lacus vel facilisis. ”</p>
  <p class="t-name" style="left:115px">Nora.K</p>
</div>

<footer class="site-footer">
  <div class="footer-brand">Vela Care</div>
  <nav class="footer-nav">
    <span class="active">Home</span><span>About Us</span><span>Services</span><span>News and Events</span><span>Career</span><span>Contact Us</span>
  </nav>
  <div class="socials" aria-label="Social links">
    <span></span><span class="on"></span><span></span><span></span>
  </div>
  <p class="copyright">© 2025 &nbsp;|&nbsp; www.velacareservices.com</p>
</footer>

</body>
</html>
```